Business card design for holistic health care clinic

We need a double-sided business card design for our holistic health care clinic that integrates our logo design and also its color scheme. My business is called Valmira. It is an integrative medicine clinic. You have already done the logo for me. Please ensure an elegant and upscale design that is not cluttered, but still has all the necessary information (please see below for details).

Target Market(s)

Wellness, fitness, rehabilitation for educated, well-traveled open-minded clients who are focused on natural, organic, balanced and preventive healthcare and lifestyle.

Industry/Entity Type

Medical

Contact Information for Business Card

Modern, clean.

Number of Pages Required

1 page

Font styles to use
Serif
Sans Serif

Colors

Designer to choose colors to be used in the design.

Requirements
Must have
• Logo on one side, all other information on the other side.
• Other information should include:
• Tobias Wrenfeld - DOE, CPT, LMT
• 4100 East Marrow Drive
• Austin, TX 78119
• 512 555 0148
• 818 555 0192
• info@ValmiraHealth.example
• t.wrenfeld@ValmiraHealth.example
Nice to have
• Darker background on front - but not totally black - shaded/dark gray.

```html
<!DOCTYPE html>
<html lang="en">
<head>
<meta charset="utf-8">
<title>Valmira Business Card</title>
<link rel="stylesheet" href="https://fonts.googleapis.com/css2?family=Roboto:wght@400;500;700&family=Roboto+Condensed:wght@500;700&display=swap">
<style>
  :root {
    --page-bg: #ecebe8;
    --card-white: #f6f6f6;
    --brand-blue: #1a8fcc;
    --brand-blue-dark: #1580bb;
    --text-grey: #4f4f4f;
    --divider: #b9b9b9;
    --white: #ffffff;
  }
  * { margin: 0; padding: 0; box-sizing: border-box; }
  html, body { width: 1200px; height: 960px; overflow: hidden; }
  body {
    background: var(--page-bg);
    position: relative;
    font-family: "Roboto", Arial, sans-serif;
  }
  .card {
    position: absolute;
    border-radius: 22px;
    overflow: hidden;
    box-shadow: 0 4px 10px rgba(0,0,0,0.25);
  }
  .card-front {
    left: 315px; top: 113px; width: 598px; height: 342px;
    background: var(--card-white);
    border-bottom: 13px solid var(--brand-blue);
  }
  .card-back {
    left: 312px; top: 472px; width: 599px; height: 342px;
    background: var(--brand-blue);
    color: var(--white);
    text-align: center;
  }
  .brand { position: absolute; text-align: center; }
  .card-front .brand { left: 40px; top: 160px; width: 265px; color: var(--brand-blue); }
  .brand-name {
    font-family: "Roboto", Arial, sans-serif;
    font-weight: 700;
    letter-spacing: 1px;
    line-height: 1;
  }
  .card-front .brand-name { font-size: 50px; }
  .brand-descriptor { font-weight: 700; }
  .card-front .brand-descriptor { font-size: 15px; margin-top: 8px; }
  .divider {
    position: absolute; left: 312px; top: 108px;
    width: 1px; height: 152px; background: var(--divider);
  }
  .contact { position: absolute; left: 336px; top: 98px; color: var(--text-grey); }
  .person-name {
    font-family: "Roboto Condensed", Arial, sans-serif;
    font-weight: 700; font-size: 20px; color: var(--brand-blue);
    text-transform: uppercase; margin-bottom: 14px;
  }
  .credentials { font-size: 12px; font-weight: 500; }
  .address { font-size: 14.5px; line-height: 18px; margin-bottom: 12px; }
  .contact-list { list-style: none; font-size: 14.5px; line-height: 19px; }
  .contact-list li { display: flex; align-items: center; gap: 9px; }
  .contact-list svg { width: 12px; height: 12px; fill: var(--brand-blue); flex: none; }
  .card-back .brand { left: 0; top: 135px; width: 100%; }
  .card-back .brand-name { font-size: 62px; }
  .card-back .brand-descriptor { font-size: 18px; margin-top: 10px; }
  .tagline { position: absolute; left: 0; top: 281px; width: 100%; font-size: 14.5px; }
</style>
</head>
<body>
  <section class="card card-front" aria-label="Card front">
    <div class="brand">
      <div class="brand-name">VALMIRA</div>
      <div class="brand-descriptor">Integrative Holistic Medicine</div>
    </div>
    <div class="divider"></div>
    <div class="contact">
      <div class="person-name">Tobias Wrenfeld <span class="credentials">- DOE, CPT, LMT</span></div>
      <p class="address">4100 East Marrow Drive<br>Austin, TX 78119</p>
      <ul class="contact-list">
        <li><svg viewBox="0 0 12 12"><path d="M2.5 0.5l2 2.4-1.1 1.4c.8 1.6 2 2.8 3.6 3.6l1.4-1.1 2.4 2-1.2 2.1C5 10.8 1.2 7 .4 1.7z"/></svg>512 555 0148</li>
        <li><svg viewBox="0 0 12 12"><path d="M3 0h6a1 1 0 0 1 1 1v10a1 1 0 0 1-1 1H3a1 1 0 0 1-1-1V1a1 1 0 0 1 1-1zm.5 1.5v7.5h5V1.5zM6 9.8a.7.7 0 1 0 0 1.4.7.7 0 0 0 0-1.4z"/></svg>818 555 0192</li>
        <li><svg viewBox="0 0 12 12"><path d="M0 2.5h12v7H0zM.8 3.2L6 7l5.2-3.8v-.1H.8z" fill-rule="evenodd"/></svg>t.wrenfeld@ValmiraHealth.example</li>
        <li><svg viewBox="0 0 12 12"><circle cx="6" cy="6" r="5.5"/><path d="M3 4.5q2-1 3 .5t3-.5M3.5 8q2 .8 5-.5" stroke="#f6f6f6" stroke-width="0.9" fill="none"/></svg>www.ValmiraHealth.example</li>
      </ul>
    </div>
  </section>

  <section class="card card-back" aria-label="Card back">
    <div class="brand">
      <div class="brand-name">VALMIRA</div>
      <div class="brand-descriptor">Integrative Holistic Medicine</div>
    </div>
    <p class="tagline">it’s all about you – your health, your objectives</p>
  </section>
</body>
</html>
```